Community-based social network needs a new landing page

We need a landing page for a local social network in Singapore called "LaneKindred.sg". It is a website that help neighbours to connect with each other for mutual benefits such as providing professional/non-professional services, sharing items, and neighbourly help, etc.

There is an existing website but we want to completely revamp it. It is most important that the new landing page communicates that the neighbourhood has skills and services for people to discover.

The final design of the landing page should be modern, and communicates a sense of community and vibrancy. As a matter of priority, more real estate should be accorded to the neighbours providing services elements.

We have drafted 2 reference sites that communicates the key ideas/user propositions for your easy reference:
http://tarvelquin8.example-sites.com/lanekindred
http://tarvelquin8.example-sites.com/lanekindred2

As long as the key ideas/user propositions are kept to, we are open to any design proposals. I.e. you do not have to follow the design layout of the reference sites

Target Market(s)

Our target market is primarily the Singapore community, includes all genders, education levels and occupations, aged between 17-45 years old.

In the file uploaded, you will find pictures of Singapore neighbourhoods and people of local ethnicities. Please use them, but you may arrange and add further filters to better enhance them

Industry/Entity Type

Real Estate

Requirements
Nice to have
• Landing page could be similar to that of www.gatherloft.com, not just at the top, but also the way the other categories are presented at the bottom.

```html
<!DOCTYPE html>
<html lang="en">
<head>
<meta charset="utf-8">
<title>LaneKindred.sg – Meet your neighbours</title>
<link href="https://fonts.googleapis.com/css2?family=Open+Sans:ital,wght@0,300;0,400;0,600;0,700;1,400&display=swap" rel="stylesheet">
<style>
:root{
  --navy:#1d2f45;
  --hero-bottom:#2b6fba;
  --ink:#1f2a36;
  --white:#ffffff;
  --link:#1c5aa6;
  --grey-text:#8a8f95;
  --lime:#9dc800;
  --footer:#1b222b;
  --footer-line:#2a333e;
  --amber:#f3b000;
  --soft:#ecedef;
  --btn-blue:#1f5fa8;
  --tag-text:#4f6e94;
  --alert-red:#d7262b;
}
*{box-sizing:border-box;margin:0;padding:0}
html,body{width:980px;height:1200px;overflow:hidden}
body{position:relative;font-family:'Open Sans',sans-serif;background:var(--white);color:var(--ink)}
.abs{position:absolute}

/* header */
.topbar{left:0;top:0;width:980px;height:54px;background:var(--navy)}
.brand{left:100px;top:14px;height:28px;padding:0 10px;background:var(--white);border-radius:4px;display:flex;align-items:center;gap:6px;font-weight:700;font-size:16px;color:var(--navy)}
.brand-dot{width:10px;height:10px;border-radius:50%;background:#e8332a}
.btn-register{left:706px;top:15px;width:68px;height:29px;background:#26405c;border:1px solid #34506f;border-radius:2px;color:#dfe8f2;font-size:11px;display:flex;align-items:center;justify-content:center;gap:5px}
.btn-login{left:783px;top:15px;width:92px;height:29px;background:#3a9be0;border-radius:2px;color:var(--white);font-size:10.5px;font-weight:700;display:flex;align-items:center;justify-content:center;gap:5px}
.sq{width:14px;height:14px;background:#2a6cb8;border-radius:2px}

/* hero */
.hero{left:0;top:54px;width:980px;height:382px;background:linear-gradient(#4d93da,var(--hero-bottom))}
.hero-skyline{left:0;top:190px;width:980px;height:246px;background:linear-gradient(rgba(120,170,225,.25),rgba(90,150,215,.5))}
.hero-band{left:0;top:436px;width:980px;height:74px;background:linear-gradient(#f3f4f6,#e4e6e9);border-bottom:1px solid #d6d8db}
.hero-title{left:92px;top:148px;font-size:41px;font-weight:600;letter-spacing:-2.5px;color:#1a2230}
.hero-lead{left:96px;top:216px;font-size:34px;line-height:40px;font-weight:600;letter-spacing:-.8px;color:var(--white)}
.btn-signup{left:122px;top:455px;width:148px;height:37px;background:linear-gradient(#72c23a,#4f9a1e);border:1px solid #3f7f17;border-radius:2px;color:var(--white);font-weight:700;font-size:14px;display:flex;align-items:center;justify-content:center}

.feature-art{left:584px;top:184px;width:254px;height:304px;background:linear-gradient(160deg,#eef1f4 0%,#e3e7ec 45%,#c9b4a2 100%)}
.feature-kicker{left:608px;top:206px;font-size:21px;color:var(--alert-red);letter-spacing:-.5px}
.feature-title{left:607px;top:228px;font-size:34px;font-weight:600;color:var(--alert-red);letter-spacing:-1px}

.tag{height:22px;padding:0 10px;background:linear-gradient(#fff,#dfe5ec);border-radius:4px;font-size:12px;font-weight:700;color:var(--tag-text);display:flex;align-items:center}
.tag-left{padding-right:24px}
.tag-right{padding-left:24px}
.avatar{width:54px;height:54px;border-radius:50%;background:radial-gradient(#ffffff 55%,#d4dbe3);border:6px solid rgba(255,255,255,.35);background-clip:padding-box;display:flex;align-items:center;justify-content:center}

/* categories */
.cat{top:555px;width:230px;text-align:center}
.cat h2{font-size:17px;font-weight:400;color:var(--link);line-height:20px;height:48px}
.cat p{font-size:10.5px;line-height:13px;color:var(--grey-text);font-weight:300;padding:0 10px}
.cat a{display:block;margin-top:14px;font-size:10px;color:var(--link);text-decoration:none}
.divider{top:520px;width:12px;height:210px;background:linear-gradient(90deg,rgba(0,0,0,.05),rgba(0,0,0,0))}

/* social strip */
.friends{left:152px;top:760px;width:188px;height:25px;background:linear-gradient(90deg,#6b5a40,#9a7a60,#404a55,#b08070,#555,#a06060)}
.social-box{left:100px;top:787px;width:240px;height:54px;background:#3b5797}
.social-name{left:63px;top:13px;font-size:21px;font-weight:700;color:var(--white);letter-spacing:-.5px}
.count{left:108px;top:776px;width:36px;height:28px;background:var(--white);border:1px solid #ccc;font-size:10px;color:#333;display:flex;align-items:center;justify-content:center}
.like{left:107px;top:810px;width:36px;height:14px;background:#e8eaee;border-radius:2px;font-size:8px;color:#9aa;display:flex;align-items:center;justify-content:center}
.talk-icon{left:363px;top:787px;width:54px;height:54px;background:var(--footer)}
.talk{left:417px;top:787px;width:462px;height:54px;background:var(--lime);color:var(--white);padding:9px 13px}
.talk strong{display:block;font-weight:300;font-size:15px}
.talk em{font-size:10px}

/* footer */
.footer{left:0;top:841px;width:980px;height:359px;background:var(--footer)}
.f-head{top:870px;font-size:15.5px;font-weight:400;color:var(--amber)}
.f-rule{left:101px;top:897px;width:780px;height:1px;background:var(--footer-line)}
.listing{left:102px;width:192px}
.listing .thumb{left:0;top:0;width:44px;height:44px;background:linear-gradient(#c9b9a4,#7b6a5a);border:2px solid #3a434e}
.listing h3{left:52px;top:-1px;font-size:12px;font-weight:400;color:var(--white);white-space:nowrap}
.listing p{left:52px;top:19px;width:140px;font-size:9.5px;line-height:13.5px;color:#8e98a4}
.meta{left:0;top:66px;width:192px;font-size:8px;color:#8e98a4;display:flex;justify-content:space-between}
.listing-rule{left:102px;top:1009px;width:192px;height:1px;background:var(--footer-line)}
.read-more{left:236px;top:1116px;font-size:9px;color:var(--lime);text-decoration:underline}
.member{width:51px;height:51px;border:2px solid #4a535e}
.signup{left:672px;top:914px;width:186px;height:224px;background:var(--white);border:6px solid #a9aeb4;padding:10px 10px}
.signup h3{font-size:19px;font-weight:400;color:var(--btn-blue);display:flex;align-items:center;gap:6px;margin-bottom:10px}
.field{height:27px;background:var(--soft);border-radius:2px;font-size:8px;font-style:italic;color:#8a8f95;padding:0 8px;display:flex;align-items:center;margin-bottom:10px}
.row{display:flex;justify-content:space-between;align-items:center;margin-top:2px;padding-bottom:14px;border-bottom:1px solid #e2e4e6}
.btn-next{width:76px;height:21px;background:var(--btn-blue);color:var(--white);font-size:11px;display:flex;align-items:center;justify-content:center}
.agree{font-size:8.5px;color:#333;display:flex;align-items:center;gap:5px}
.agree i{width:10px;height:10px;border:1px solid var(--btn-blue)}
.links{font-size:9px;line-height:15px;color:#333;margin-top:12px;padding-left:2px}
.copyright{left:106px;top:1176px;font-size:9.5px;color:#8e98a4}
.bottom-rule{left:101px;top:1167px;width:780px;height:1px;background:var(--footer-line)}
</style>
</head>
<body>

<header class="abs topbar">
  <div class="abs brand"><span class="brand-dot"></span>LaneKindred.sg</div>
  <div class="abs btn-register">
    <svg width="10" height="10" viewBox="0 0 10 10" fill="#3ea3e6"><rect x="0" y="0" width="2.5" height="2.5"/><rect x="3.7" y="0" width="2.5" height="2.5"/><rect x="7.4" y="0" width="2.5" height="2.5"/><rect x="0" y="3.7" width="2.5" height="2.5"/><rect x="3.7" y="3.7" width="2.5" height="2.5"/><rect x="7.4" y="3.7" width="2.5" height="2.5"/><rect x="0" y="7.4" width="2.5" height="2.5"/><rect x="3.7" y="7.4" width="2.5" height="2.5"/></svg>
    Register
  </div>
  <div class="abs btn-login">LOG IN <span class="sq"></span><span class="sq"></span></div>
</header>

<section class="abs hero"></section>
<div class="abs hero-skyline" role="img" aria-label="Soft city skyline and clouds behind the headline"></div>
<div class="abs hero-band"></div>

<h1 class="abs hero-title">What Do You Need?</h1>
<p class="abs hero-lead">Crowd source from the<br>50,000 people living<br>around you</p>
<div class="abs btn-signup">Sign up. It’s free!</div>

<svg class="abs" style="left:440px;top:130px" width="440" height="270" viewBox="0 0 440 270" fill="none" stroke="rgba(255,255,255,.75)" stroke-width="1.4">
  <path d="M150 20 C 190 5, 220 15, 230 55"/>
  <path d="M420 75 C 440 130, 430 200, 400 240"/>
  <path d="M90 230 C 120 250, 150 240, 160 230"/>
</svg>

<div class="abs feature-art" role="img" aria-label="Book cover showing a smiling young man beside a network of neighbour portraits"></div>
<div class="abs feature-kicker">Meet People In</div>
<div class="abs feature-title">Singapore</div>

<div class="abs tag tag-left" style="left:480px;top:159px">Michael</div>
<div class="abs avatar" style="left:532px;top:142px"><svg width="22" height="22" viewBox="0 0 22 22" fill="#1a1a1a"><circle cx="11" cy="7" r="5"/><path d="M2 21c0-6 4-8 9-8s9 2 9 8z"/></svg></div>

<div class="abs tag tag-right" style="left:838px;top:173px">Samir</div>
<div class="abs avatar" style="left:804px;top:157px"><svg width="22" height="22" viewBox="0 0 22 22" fill="#1a1a1a"><circle cx="11" cy="7" r="5"/><path d="M2 21c0-6 4-8 9-8s9 2 9 8z"/></svg></div>

<div class="abs tag tag-left" style="left:443px;top:322px">Peter</div>
<div class="abs avatar" style="left:482px;top:305px"><svg width="22" height="22" viewBox="0 0 22 22" fill="#1a1a1a"><circle cx="11" cy="7" r="5"/><path d="M2 21c0-6 4-8 9-8s9 2 9 8z"/></svg></div>

<div class="abs divider" style="left:348px"></div>
<div class="abs divider" style="left:619px"></div>

<section class="abs cat" style="left:91px">
  <h2>Professional Services</h2>
  <p>Lorem Ipsum is simply dummy text of the printing and typesetting industry. Lorem Ipsum has been the industry's standard dummy text</p>
  <a href="#">[ Read More.... ]</a>
</section>
<section class="abs cat" style="left:357px">
  <h2>Non Professional</h2>
  <p>Lorem Ipsum is simply dummy text of the printing and typesetting industry. Lorem Ipsum has been the industry's standard dummy text</p>
  <a href="#">[ Read More.... ]</a>
</section>
<section class="abs cat" style="left:636px">
  <h2>Selling, helping, Lending<br>and borrowing</h2>
  <p>Lorem Ipsum is simply dummy text of the printing and typesetting industry. Lorem Ipsum has been the industry's standard dummy text</p>
  <a href="#">[ Read More.... ]</a>
</section>

<div class="abs friends" role="img" aria-label="Row of small friend profile pictures"></div>
<div class="abs social-box"><span class="abs social-name">Linkwall</span></div>
<div class="abs count">90m</div>
<div class="abs like">✓ Like</div>

<div class="abs talk-icon">
  <svg width="54" height="54" viewBox="0 0 54 54" fill="#fff"><path d="M20 18h16v10h-6l-4 4v-4h-6z"/><path d="M15 24h12v8h-5l-3 3v-3h-4z" stroke="#1b222b" stroke-width="1.5"/></svg>
</div>
<div class="abs talk"><strong>Yes, let’s talk business!</strong><em>Please reach out and a business representative will get back to you.</em></div>

<footer class="abs footer"></footer>
<h2 class="abs f-head" style="left:101px">Latest Listings</h2>
<h2 class="abs f-head" style="left:394px">Latest Members</h2>
<h2 class="abs f-head" style="left:677px">Join Us</h2>
<div class="abs f-rule"></div>

<article class="abs listing" style="top:911px">
  <div class="abs thumb" role="img" aria-label="Member portrait"></div>
  <h3 class="abs">Lorem Ipsum is simply</h3>
  <p class="abs">Lorem Ipsum is simply dummy text of the printing</p>
  <div class="abs meta"><span>5 Comments</span><span>👍 👎</span><span>04 July 2013</span></div>
</article>
<div class="abs listing-rule"></div>
<article class="abs listing" style="top:1032px">
  <div class="abs thumb" role="img" aria-label="Member portrait" style="background:linear-gradient(#e8c890,#b08a5c)"></div>
  <h3 class="abs">Lorem Ipsum is simply</h3>
  <p class="abs">Lorem Ipsum is simply dummy text of the printing</p>
  <div class="abs meta"><span>5 Comments</span><span>👍 👎</span><span>04 July 2013</span></div>
</article>
<a class="abs read-more" href="#">Read More</a>

<div class="abs member" style="left:396px;top:915px;background:linear-gradient(#4a8a3a,#d9c040)" role="img" aria-label="Member picture"></div>
<div class="abs member" style="left:454px;top:915px;background:linear-gradient(#b09070,#6a7a8a)" role="img" aria-label="Member picture"></div>
<div class="abs member" style="left:512px;top:915px;background:linear-gradient(#d8dcdc,#8fc0b8)" role="img" aria-label="Member picture"></div>
<div class="abs member" style="left:396px;top:973px;background:linear-gradient(#5a5048,#1a1a1a)" role="img" aria-label="Member picture"></div>
<div class="abs member" style="left:454px;top:973px;background:linear-gradient(#a8c0d4,#6a5040)" role="img" aria-label="Member picture"></div>
<div class="abs member" style="left:512px;top:973px;background:linear-gradient(#f0d0b0,#e86090)" role="img" aria-label="Member picture"></div>
<div class="abs member" style="left:396px;top:1031px;background:linear-gradient(#4a8a3a,#d9c040)" role="img" aria-label="Member picture"></div>
<div class="abs member" style="left:454px;top:1031px;background:linear-gradient(#b09070,#6a7a8a)" role="img" aria-label="Member picture"></div>
<div class="abs member" style="left:512px;top:1031px;background:linear-gradient(#d8dcdc,#8fc0b8)" role="img" aria-label="Member picture"></div>

<form class="abs signup">
  <h3><svg width="16" height="20" viewBox="0 0 16 20" fill="none" stroke="#1f5fa8" stroke-width="1.6"><rect x="1" y="1" width="12" height="17"/><path d="M4 6h6M4 9h6M4 12h6"/></svg>Sign Up</h3>
  <div class="field">Enter User Name:</div>
  <div class="field">Enter Your Password:</div>
  <div class="row"><div class="btn-next">Next</div><div class="agree">I Agree <i></i></div></div>
  <div class="links">Forgot Password?<br>Resend Activation Code</div>
</form>

<div class="abs bottom-rule"></div>
<p class="abs copyright">© 2013 LaneKindred. All Rights Reserved.</p>

</body>
</html>
```